TLR PowerPoint

I am looking for a clean, corporate PowerPoint template.

I would like the following:
- title slide
- break slide
- blank slide with title (for graphs or graphics)
- an ending slide.

Target Market(s)

Business professionals, medium to large business clients.

Requirements
Must have
• Must incorporate the TLR logo in either the header or footer

```html
<!DOCTYPE html>
<html lang="en">
<head>
<meta charset="utf-8">
<title>TLR Slide – Bullet Form</title>
<link rel="stylesheet" href="https://fonts.googleapis.com/css2?family=Graduate&family=Cinzel:wght@400;600&family=Open+Sans:wght@400;600&display=swap">
<style>
  :root {
    --page: #ffffff;
    --slide-light: #f1f1f1;
    --slide-mid: #dcdcdc;
    --accent: #27a6e1;
    --ink: #2b2b2b;
    --band: #1d1d1d;
    --white: #ffffff;
  }
  * { margin: 0; padding: 0; box-sizing: border-box; }
  html, body { width: 1200px; height: 900px; overflow: hidden; background: var(--page); }
  .canvas { position: relative; width: 1200px; height: 900px; }

  .slide {
    position: absolute; left: 43px; top: 170px; width: 1114px; height: 627px;
    overflow: hidden;
  }
  .slide-texture {
    position: absolute; inset: 0;
    background: radial-gradient(ellipse at 60% 35%, var(--slide-light) 0%, #e6e6e6 55%, var(--slide-mid) 100%);
  }

  .rule-svg { position: absolute; left: 14px; top: 22px; }
  .page-corner { position: absolute; right: 15px; top: 13px; }
  .page-number {
    position: absolute; right: 28px; top: 30px;
    font-family: "Graduate", serif; font-size: 22px; color: var(--white);
    -webkit-text-stroke: 1px var(--white);
  }

  .main-bullet {
    position: absolute; left: 104px; top: 95px;
    display: flex; align-items: center; gap: 16px;
  }
  .main-bullet-text {
    display: inline-block;
    font-family: "Graduate", serif; font-size: 44px; color: var(--accent);
    line-height: 1; letter-spacing: 0;
    -webkit-text-stroke: 1.5px var(--accent);
    transform: scaleX(0.9); transform-origin: left center;
  }
  .sub-bullets { position: absolute; left: 190px; top: 145px; list-style: none; }
  .sub-bullet {
    display: flex; align-items: center; gap: 10px; height: 55px;
    font-family: "Cinzel", serif; font-size: 23px; color: var(--ink);
  }

  .footer-band {
    position: absolute; left: 16px; top: 476px; width: 1083px; height: 139px;
    background: var(--band);
  }
  .slide-title {
    position: absolute; left: 21px; top: 16px;
    font-family: "Graduate", serif; font-size: 72px; line-height: 1; font-weight: 400;
    color: var(--accent); letter-spacing: 0; white-space: nowrap;
    -webkit-text-stroke: 2px var(--accent);
    transform: scaleX(0.92); transform-origin: left top;
  }
  .title-rule {
    position: absolute; left: 23px; top: 88px; width: 407px; height: 3px; background: var(--white);
  }
  .slide-subtitle {
    position: absolute; left: 23px; top: 100px; width: 408px; text-align: right;
    font-family: "Open Sans", sans-serif; font-size: 17px; color: var(--white);
  }
  .contact {
    position: absolute; right: 167px; top: 57px; text-align: right;
    font-family: "Open Sans", sans-serif; font-size: 10.5px; line-height: 16px; color: var(--white);
  }
  .brand-box {
    position: absolute; right: 9px; top: 10px; width: 143px; height: 119px;
    background: var(--white); display: flex; align-items: center; justify-content: center;
  }
  .brand-name {
    font-family: "Open Sans", sans-serif; font-weight: 600; font-size: 30px;
    letter-spacing: 2px; color: var(--band);
  }
</style>
</head>
<body>
<main class="canvas">
  <section class="slide">
    <div class="slide-texture" role="img" aria-label="Soft light grey paper texture background"></div>

    <svg class="rule-svg" width="1010" height="50" viewBox="0 0 1010 50" aria-hidden="true">
      <rect x="12" y="12" width="26" height="26" rx="4" transform="rotate(45 25 25)" fill="var(--white)" stroke="var(--ink)" stroke-width="3"/>
      <circle cx="25" cy="25" r="8" fill="var(--accent)"/>
      <line x1="46" y1="24" x2="1005" y2="24" stroke="var(--ink)" stroke-width="4"/>
    </svg>

    <svg class="page-corner" width="100" height="99" viewBox="0 0 100 99" aria-hidden="true">
      <polygon points="0,0 100,0 100,99" fill="var(--accent)"/>
    </svg>
    <div class="page-number">03</div>

    <div class="main-bullet">
      <svg width="40" height="38" viewBox="0 0 40 38" aria-hidden="true">
        <polygon points="11,3 29,3 37,19 29,35 11,35 3,19" transform="rotate(15 20 19)" fill="none" stroke="var(--accent)" stroke-width="5"/>
      </svg>
      <span class="main-bullet-text">MAIN BULLET</span>
    </div>

    <ul class="sub-bullets">
      <li class="sub-bullet">
        <svg width="34" height="32" viewBox="0 0 34 32" aria-hidden="true"><polygon points="9,3 25,3 31,16 25,29 9,29 3,16" transform="rotate(15 17 16)" fill="var(--accent)" stroke="var(--ink)" stroke-width="4"/></svg>
        SUB BULLET FORM
      </li>
      <li class="sub-bullet">
        <svg width="34" height="32" viewBox="0 0 34 32" aria-hidden="true"><polygon points="9,3 25,3 31,16 25,29 9,29 3,16" transform="rotate(15 17 16)" fill="var(--accent)" stroke="var(--ink)" stroke-width="4"/></svg>
        SUB BULLET FORM
      </li>
      <li class="sub-bullet">
        <svg width="34" height="32" viewBox="0 0 34 32" aria-hidden="true"><polygon points="9,3 25,3 31,16 25,29 9,29 3,16" transform="rotate(15 17 16)" fill="var(--accent)" stroke="var(--ink)" stroke-width="4"/></svg>
        SUB BULLET FORM
      </li>
    </ul>

    <footer class="footer-band">
      <h1 class="slide-title">SLIDE TITLE</h1>
      <div class="title-rule"></div>
      <p class="slide-subtitle">BULLET FORM</p>
      <p class="contact">WWW.COMPANYSITE.COM<br>COMPANY@COMPANY.COM</p>
      <div class="brand-box"><span class="brand-name">TLR</span></div>
    </footer>
  </section>
</main>
</body>
</html>
```